Business Card Design Project

We are a construction company in Orange County, CA. We need a two sided business card. We would like the back to be our logo with web URL. Front should included Name, title, address, phone, fax and email address.

our address is
627 West Dorrance Blvd, Suite 308
Anaheim, CA 92718

Our logo files are attached.

Construction

```html
<!DOCTYPE html>
<html lang="en">
<head>
<meta charset="utf-8">
<title>KORVAN Business Card</title>
<link rel="stylesheet" href="https://fonts.googleapis.com/css2?family=Source+Sans+3:ital,wght@0,400;0,600;0,700;1,700&display=swap">
<style>
  :root {
    --brand-blue: #134a7c;
    --ink: #333333;
    --rule: #3a3a3a;
    --paper: #ffffff;
    --back-light: #3b3636;
    --back-dark: #000000;
    --stage: #dcdcdc;
  }
  * { margin: 0; padding: 0; box-sizing: border-box; }
  html, body {
    width: 960px; height: 1200px; overflow: hidden;
    background: var(--stage);
    font-family: "Source Sans 3", "Myriad Pro", Arial, sans-serif;
  }
  .canvas { position: relative; width: 960px; height: 1200px; }
  .card {
    position: absolute; left: 60px; width: 840px; height: 480px;
    border-radius: 30px; overflow: hidden;
  }
  .card-front { top: 85px; background: var(--paper); }
  .card-back {
    top: 645px;
    background: linear-gradient(90deg, var(--back-light) 0%, var(--back-light) 45%, var(--back-dark) 100%);
  }
  .wordmark {
    position: absolute; left: 0; right: 0; text-align: center;
    font-weight: 700; line-height: 1; letter-spacing: 2px;
  }
  .card-front .wordmark { top: 62px; font-size: 150px; color: var(--brand-blue); }
  .card-back .wordmark { top: 145px; font-size: 170px; color: var(--paper); }
  .tagline {
    position: absolute; left: 0; right: 0; text-align: center;
    font-weight: 600; text-transform: uppercase; line-height: 1;
  }
  .card-front .tagline { top: 198px; font-size: 21px; letter-spacing: 5.5px; color: var(--brand-blue); }
  .card-back .tagline { top: 302px; font-size: 24px; letter-spacing: 6.5px; color: var(--paper); }
  .contact {
    position: absolute; top: 278px; left: 0; right: 0; text-align: center;
    color: var(--ink); font-size: 22px; line-height: 34px;
  }
  .contact .label { font-weight: 700; font-style: italic; }
  .contact .address { margin-top: 10px; }
  .divider {
    position: absolute; top: 410px; left: 0; right: 0; height: 3px; background: var(--rule);
  }
  .name-band {
    position: absolute; top: 420px; left: 0; right: 0; height: 60px;
    background: var(--brand-blue); color: var(--paper);
    display: flex; align-items: center; justify-content: center; gap: 6px;
  }
  .name-band .person { font-size: 26px; font-weight: 600; }
  .name-band .title { font-size: 21px; font-weight: 600; }
  .web {
    position: absolute; top: 400px; left: 0; right: 0; text-align: center;
    color: var(--paper); font-size: 29px; font-weight: 600;
  }
</style>
</head>
<body>
<main class="canvas">
  <section class="card card-front" aria-label="Card front">
    <div class="wordmark">KORVAN</div>
    <div class="tagline">Plan • Develop • Construct</div>
    <div class="contact">
      <div><span class="label">p</span> : 1-234-4567 &nbsp;|&nbsp; <span class="label">f</span> : 1-234-4567</div>
      <div><span class="label">e</span> : info@korvanmail.com &nbsp;|&nbsp; <span class="label">w</span> : www.korvanbuild.com</div>
      <div class="address">627 West Dorrance Blvd, Suite 308, Anaheim, CA 92718</div>
    </div>
    <div class="divider"></div>
    <div class="name-band"><span class="person">Your Name,</span><span class="title">Designation</span></div>
  </section>

  <section class="card card-back" aria-label="Card back">
    <div class="wordmark">KORVAN</div>
    <div class="tagline">Plan • Develop • Construct</div>
    <div class="web">www.korvanbuild.com</div>
  </section>
</main>
</body>
</html>
```